Growing Plumbing company requires signage for vans/trucks plus letterhead and business cards

Pelkey's Plumbing and Heating (see www.pelkeysnf.ca) is a well established plumbing and heating company that has been servicing the new construction, renovation and plumbing maintenance needs of residential and commercial clients for over 40 years. It operates in St. John's, Newfoundland and Labrador, Canada..

The company is now expanding into a new line of business (electrical contracting) and requires a slight modification to its existing logo. The change is from "Pelkey's Plumbing and Heating" to "Pelkey's Plumbing and Electrical". An existing raw data file is provided to allow for this slight change. NO OTHER CHANGE TO THE LOGO IS REQUIRED.

As a result of this logo change, the company would like to create a new corporate identity package that includes the following:

- Signage for company vans (sample provided with new suggestions requested)

- Signage for company trucks (simple sign on driver and passenger doors and on tailgate) (no sample exists).

- Corporate letter head (sample provided with new suggestions requested)

- Business cards (sample provided with new suggestions requested)
Updates

Hello all, 

To clarify: work on the corporate logo only requires the word change from "Heating" to "Electric". No other changes are requested on the logo. ie no changes to "D", etc. 

As a result of this slight logo change, we are also requesting suggestions that could be made to existing corporate signage, letterhead, etc. 

Thanks, 

The Pelkey's Team. 

The exact font files to be used have been uploaded.

To clarify on corporate name: 

It is to be "Pelkey's Plumbing and Electrical"   (Not Heating or Electric)

The Pelkey's Team

Industry/Entity Type

Residential

Logo Text

Pelkey's Plumbing and Electrical

Requirements
Must have
• For van and truck signage, we want something that is "clean". Phone number, website, and logo must be included.

For logo, except for change from "heating" to "electrical" no other changes are requested.

For the logo change, we will require logo to be provided for all reproduction requirements including vertical (stacked) and horizontal treatments; black & white / colour / reverse; file formats including vector (designer use) and jpeg/pdf/gif, etc. (user use); variety of sizes in all files (i.e. small, medium and large).
Nice to have
• An idea would be to have the business cards, signage and letterhead use the grey bars in the "D" of the logo as a background or to the side.

```html
<!DOCTYPE html>
<html lang="en">
<head>
<meta charset="utf-8">
<title>Pelkey's Plumbing and Electrical – Business Cards</title>
<link href="https://fonts.googleapis.com/css2?family=Roboto:wght@300;400;700&display=swap" rel="stylesheet">
<style>
  :root {
    --page: #d9dadb;
    --card: #e9eaeb;
    --navy: #123c6e;
    --grey-text: #6d6f72;
    --dark-text: #3f4144;
  }
  html, body {
    margin: 0;
    width: 1200px;
    height: 900px;
    overflow: hidden;
    background: var(--page);
    font-family: "Roboto", Arial, sans-serif;
  }
  .sheet {
    position: relative;
    width: 1200px;
    height: 900px;
  }
  .card {
    position: absolute;
    width: 640px;
    height: 366px;
    background: var(--card);
    box-shadow: 0 6px 18px rgba(0,0,0,.18);
    overflow: hidden;
  }
  .card--front { left: 140px; top: 50px; }
  .card--back  { left: 420px; top: 470px; }

  .stripe {
    position: absolute;
    left: 58px;
    right: 0;
    bottom: 26px;
    height: 20px;
    background: var(--navy);
  }

  .wordmark {
    position: absolute;
    color: var(--navy);
    font-weight: 700;
    text-transform: uppercase;
    line-height: 1;
    margin: 0;
  }
  .wordmark__name { display: block; letter-spacing: .5px; }
  .wordmark__line { display: block; letter-spacing: 1px; margin-top: 4px; }
  .wordmark__dot {
    position: absolute;
    left: -44px;
    top: 2px;
    width: 32px;
    height: 32px;
    background: var(--navy);
  }

  .card--front .wordmark { left: 250px; top: 110px; }
  .card--front .wordmark__name { font-size: 44px; }
  .card--front .wordmark__line { font-size: 16.5px; }
  .card--front .wordmark__dot { left: -54px; width: 40px; height: 40px; }

  .card--back .wordmark { left: 92px; top: 50px; }
  .card--back .wordmark__name { font-size: 34px; }
  .card--back .wordmark__line { font-size: 12.8px; }

  .person {
    position: absolute;
    left: 48px;
    top: 190px;
  }
  .person__name {
    margin: 0;
    font-weight: 300;
    font-size: 24px;
    color: var(--grey-text);
    text-transform: uppercase;
    letter-spacing: .5px;
  }
  .person__role {
    margin: 4px 0 0;
    font-size: 15px;
    font-weight: 400;
    color: var(--grey-text);
  }

  .website {
    position: absolute;
    left: 48px;
    bottom: 62px;
    font-size: 15px;
    font-weight: 400;
    color: var(--navy);
  }

  .contact {
    position: absolute;
    left: 420px;
    top: 56px;
    font-size: 13px;
    color: var(--dark-text);
    line-height: 1.45;
    font-style: normal;
  }
  .contact__row { display: flex; gap: 14px; }
  .contact__label { width: 10px; }
  .contact__address { margin-top: 14px; padding-left: 24px; }
</style>
</head>
<body>
  <main class="sheet">
    <section class="card card--front" aria-label="Business card front">
      <h1 class="wordmark">
        <span class="wordmark__dot"></span>
        <span class="wordmark__name">Pelkey's</span>
        <span class="wordmark__line">Plumbing and Electrical</span>
      </h1>
      <div class="stripe"></div>
    </section>

    <section class="card card--back" aria-label="Business card back">
      <p class="wordmark">
        <span class="wordmark__dot"></span>
        <span class="wordmark__name">Pelkey's</span>
        <span class="wordmark__line">Plumbing and Electrical</span>
      </p>

      <div class="person">
        <p class="person__name">Clara Whitmore</p>
        <p class="person__role">Director</p>
      </div>

      <address class="contact">
        <div class="contact__row"><span class="contact__label">T</span><span>709.555.0142</span></div>
        <div class="contact__row"><span class="contact__label">E</span><span>info@pelkeysnf.ca</span></div>
        <div class="contact__address">
          48 Harbourview Rd<br>
          Paradise NL<br>
          A1L 0X9
        </div>
      </address>

      <p class="website">www.pelkeysnf.ca</p>
      <div class="stripe"></div>
    </section>
  </main>
</body>
</html>
```